ready mix concrete business

i need a logo for a ready mix company
it is called Lower Tenbrook Concrete for business cards and promotional items. would like a ready mix truck on it
and must look profesional

```html
<!DOCTYPE html>
<html lang="en">
<head>
<meta charset="utf-8">
<title>Lower Tenbrook Concrete – Business Card</title>
<link rel="stylesheet" href="https://fonts.googleapis.com/css2?family=Exo+2:wght@400;700&family=Open+Sans:wght@400;600&display=swap">
<style>
  :root {
    --page-bg: #e9eaec;
    --card-light: #dde0e3;
    --card-mid: #a7a9ac;
    --card-dark: #8c8e91;
    --brand-blue: #1b72bd;
    --text-white: #ffffff;
    --text-soft: #f3f4f5;
  }
  html, body {
    margin: 0;
    padding: 0;
    width: 1200px;
    height: 826px;
    overflow: hidden;
    background: var(--page-bg);
  }
  .canvas {
    position: relative;
    width: 1200px;
    height: 826px;
  }
  .business-card {
    position: absolute;
    left: 75px;
    top: 113px;
    width: 1050px;
    height: 600px;
    overflow: hidden;
    border-radius: 6px;
    box-shadow: 0 10px 30px rgba(0,0,0,0.18);
    background: var(--card-mid);
  }
  .card-shapes {
    position: absolute;
    inset: 0;
  }
  .brand {
    position: absolute;
    left: 70px;
    top: 112px;
    display: flex;
    align-items: center;
    gap: 24px;
  }
  .brand-mark {
    width: 74px;
    height: 74px;
    background: var(--brand-blue);
  }
  .brand-divider {
    width: 3px;
    height: 140px;
    background: var(--brand-blue);
  }
  .brand-name {
    font-family: "Exo 2", sans-serif;
    font-weight: 700;
    color: var(--brand-blue);
    font-size: 44px;
    line-height: 1.05;
    letter-spacing: 1px;
    text-transform: uppercase;
  }
  .person {
    position: absolute;
    left: 60px;
    top: 430px;
    display: flex;
    align-items: center;
    gap: 22px;
  }
  .avatar-ring {
    width: 64px;
    height: 64px;
    border-radius: 50%;
    border: 4px solid var(--text-white);
    background: var(--card-dark);
  }
  .person-name {
    font-family: "Exo 2", sans-serif;
    font-size: 26px;
    color: var(--text-white);
    letter-spacing: 1px;
    text-transform: uppercase;
  }
  .person-role {
    font-family: "Open Sans", sans-serif;
    font-size: 16px;
    color: var(--text-soft);
  }
  .contact-list {
    position: absolute;
    left: 800px;
    top: 236px;
    margin: 0;
    padding: 0;
    list-style: none;
    font-family: "Open Sans", sans-serif;
    font-size: 15px;
    color: var(--text-white);
  }
  .contact-list li {
    display: flex;
    align-items: center;
    gap: 10px;
    height: 30px;
    white-space: nowrap;
  }
  .contact-icon {
    width: 20px;
    height: 20px;
    flex: none;
  }
  .website {
    position: absolute;
    right: 70px;
    bottom: 34px;
    font-family: "Open Sans", sans-serif;
    font-size: 24px;
    color: var(--text-white);
    letter-spacing: 0.5px;
  }
</style>
</head>
<body>
<div class="canvas">
  <div class="business-card">
    <svg class="card-shapes" width="1050" height="600" viewBox="0 0 1050 600" aria-hidden="true">
      <polygon points="0,0 1050,0 1050,40 330,420 0,420" fill="var(--card-light)"/>
      <polygon points="420,372.5 580,470 780,182.4" fill="var(--card-dark)"/>
      <polygon points="470,346 580,425 725,211.4" fill="var(--card-mid)"/>
      <line x1="1050" y1="40" x2="330" y2="420" stroke="var(--brand-blue)" stroke-width="4"/>
      <path d="M0,600 L0,566 L520,566 Q560,566 590,540 Q620,515 660,515 L1050,515 L1050,600 Z" fill="var(--brand-blue)"/>
    </svg>

    <div class="brand">
      <div class="brand-mark"></div>
      <div class="brand-divider"></div>
      <div class="brand-name">Lower Tenbrook<br>Concrete</div>
    </div>

    <ul class="contact-list">
      <li>
        <svg class="contact-icon" viewBox="0 0 20 20" aria-hidden="true"><circle cx="10" cy="10" r="10" fill="var(--brand-blue)"/><path d="M6.5 5.5 L8.5 5.5 L9.2 7.8 L8 8.8 Q9 11 11.2 12 L12.2 10.8 L14.5 11.5 L14.5 13.5 Q9 14.5 6.5 5.5Z" fill="#fff"/></svg>
        <span>123 456 7890</span>
      </li>
      <li>
        <svg class="contact-icon" viewBox="0 0 20 20" aria-hidden="true"><circle cx="10" cy="10" r="10" fill="var(--brand-blue)"/><rect x="7" y="4.5" width="6" height="11" rx="1.2" fill="#fff"/></svg>
        <span>123 456 7890</span>
      </li>
      <li>
        <svg class="contact-icon" viewBox="0 0 20 20" aria-hidden="true"><circle cx="10" cy="10" r="10" fill="var(--brand-blue)"/><rect x="5" y="6.5" width="10" height="7" fill="#fff"/><polyline points="5,6.5 10,10.5 15,6.5" fill="none" stroke="var(--brand-blue)" stroke-width="1.2"/></svg>
        <span>yourmail@tenbrookmail.com</span>
      </li>
      <li>
        <svg class="contact-icon" viewBox="0 0 20 20" aria-hidden="true"><circle cx="10" cy="10" r="10" fill="var(--brand-blue)"/><polygon points="10,4.5 15.5,9.5 14,9.5 14,15 6,15 6,9.5 4.5,9.5" fill="#fff"/></svg>
        <span>1234, Street name, Area</span>
      </li>
    </ul>

    <div class="person">
      <div class="avatar-ring"></div>
      <div>
        <div class="person-name">Your Name</div>
        <div class="person-role">Post</div>
      </div>
    </div>

    <div class="website">yourwebsite.com</div>
  </div>
</div>
</body>
</html>
```